Herbalist's Pain Cream WIX Website Redesign

I need a complete WIX website redesign! I am an herbalist and I'm relaunching my company, starting with a pain cream as the flagship product. My natural pain relief cream is composed of 6 active botanicals, uses all natural preservatives and provides pain relief within 1 minute! I have a new label design that reflects the high quality of this product and its ingredients. I have the content written and a rough website outline. I want the new website to match the color scheme of the label, and to show the quality of the product. (Logo uploaded is older color scheme. See New Label upload for updated color scheme.) I will be launching more products in the future, but the current content is for 1 flagship product. I want a high quality, earthy/ natural, botanical medicine feel. SEO phrase "Natural Pain Relief Cream" Old website is up again, for pictures: www.fennowroots.com

Target Market(s)

Middle to later aged women, Same for Men, but usually introduced by woman in their life

Industry/Entity Type

Botanical Supplement

Coding

Coded - Design and coding required

Number of Pages Required

5+ page

Colors
0054AA
0677BA
7BADD7
CADEEF
E8F1F8

Requirements
Must have
• Homepage, About, Ingredients, Shop, Contact Us
Nice to have
• FAQ section, maybe graphics to highlight unique elements

```html
<!DOCTYPE html>
<html lang="en">
<head>
<meta charset="utf-8">
<title>Fennow Roots – Natural Pain Relief Cream</title>
<link rel="stylesheet" href="https://fonts.googleapis.com/css2?family=Montserrat:wght@300;400;500;600;700;800&display=swap">
<style>
  :root {
    --blue-deep: #0054AA;
    --blue: #0677BA;
    --blue-mid: #7BADD7;
    --blue-soft: #CADEEF;
    --blue-pale: #E8F1F8;
    --ink: #1d1d1f;
    --card: #efefef;
    --dark: #2b2b2b;
    --white: #ffffff;
  }
  * { margin: 0; padding: 0; box-sizing: border-box; }
  html, body { width: 1200px; height: 2466px; overflow: hidden; }
  body { font-family: "Montserrat", sans-serif; color: var(--ink); background: var(--white); position: relative; }

  .site-header { position: absolute; top: 0; left: 0; width: 1200px; height: 69px; background: var(--white); }
  .brand { position: absolute; left: 102px; top: 20px; display: flex; align-items: center; gap: 10px; }
  .brand-dot { width: 22px; height: 22px; border-radius: 50%; background: var(--blue); }
  .brand-name { font-size: 22px; font-weight: 500; color: var(--blue); letter-spacing: 0.5px; }
  .main-nav { position: absolute; top: 27px; left: 395px; display: flex; gap: 0; font-size: 11px; font-weight: 500; }
  .main-nav a { color: var(--ink); text-decoration: none; position: absolute; white-space: nowrap; }
  .search-box { position: absolute; left: 745px; top: 18px; width: 187px; height: 32px; border: 1px solid #555; border-radius: 4px; display: flex; align-items: center; padding-left: 10px; gap: 7px; font-size: 11px; }
  .header-icons { position: absolute; top: 22px; left: 0; }
  .header-icons > * { position: absolute; }
  .avatar { left: 1048px; width: 24px; height: 24px; border-radius: 50%; background: #1a1a1a; }

  .hero { position: absolute; top: 69px; left: 0; width: 1200px; height: 510px;
    background: radial-gradient(ellipse at 75% 50%, #3ab4f0 0%, #1c93e0 35%, #0a6fcc 65%, #0452a8 100%); }
  .hero::after { content: ""; position: absolute; left: 0; bottom: 0; width: 100%; height: 140px; background: linear-gradient(180deg, rgba(120,210,250,0) 0%, rgba(130,215,250,0.55) 100%); }
  .hero-title { position: absolute; left: 104px; top: 152px; font-size: 54px; line-height: 47px; font-weight: 800; color: var(--white); letter-spacing: -0.5px; z-index: 1; }
  .hero-sub { position: absolute; left: 104px; top: 268px; font-size: 22px; line-height: 27px; font-weight: 400; color: var(--white); z-index: 1; }
  .product-shot { position: absolute; border-radius: 14px; background: linear-gradient(180deg, #fbfbfb 0%, #f0f0f0 22%, #c7d8ea 24%, #b4cbe3 70%, rgba(190,210,230,0.35) 100%); }
  .hero .product-shot { left: 724px; top: 103px; width: 319px; height: 393px; z-index: 1; }

  .features { position: absolute; top: 579px; left: 0; width: 1200px; height: 483px; background: var(--white); }
  .feature { position: absolute; top: 100px; width: 340px; text-align: center; }
  .feature svg { display: block; margin: 0 auto; }
  .feature h3 { margin-top: 26px; font-size: 27px; line-height: 26px; font-weight: 700; }
  .feature p { margin-top: 30px; font-size: 18px; line-height: 28.7px; font-weight: 400; }

  .difference { position: absolute; top: 1062px; left: 0; width: 1200px; height: 548px; background: #e3eef9; }
  .difference h2 { position: absolute; left: 106px; top: 153px; font-size: 43px; line-height: 39px; font-weight: 800; letter-spacing: -0.5px; }
  .difference p { position: absolute; left: 106px; top: 244px; width: 420px; font-size: 16.5px; line-height: 19px; }
  .btn-shop { position: absolute; left: 106px; top: 357px; width: 113px; height: 38px; border-radius: 3px; background: var(--blue); color: var(--white); font-size: 10.5px; font-weight: 700; display: flex; align-items: center; justify-content: center; }
  .difference .product-shot { left: 732px; top: 125px; width: 316px; height: 382px; }

  .testimonials { position: absolute; top: 1610px; left: 0; width: 1200px; height: 428px; }
  .testimonials h2 { position: absolute; left: 38px; top: 48px; font-size: 23px; font-weight: 700; }
  .quote-card { position: absolute; top: 108px; width: 364px; height: 272px; background: var(--card); padding: 36px 29px 0; }
  .quote-card h4 { font-size: 21.5px; line-height: 25px; font-weight: 700; color: var(--blue); }
  .quote-card p { margin-top: 6px; font-size: 11.2px; line-height: 13.5px; color: #333; }
  .quote-card .author { margin-top: 26px; font-size: 11.2px; font-weight: 700; }

  .contact-band { position: absolute; top: 2038px; left: 0; width: 1200px; height: 428px; background: var(--dark); color: var(--white); text-align: center; }
  .contact-band h2 { margin-top: 48px; font-size: 37px; line-height: 37px; font-weight: 700; }
  .contact-band p { width: 560px; margin: 14px auto 0; font-size: 14px; line-height: 21px; font-weight: 400; }
  .btn-contact { display: block; width: 193px; height: 37px; margin: 20px auto 0; background: var(--white); color: var(--ink); border: 1px solid #888; font-size: 13px; line-height: 35px; }
  .footer-brand { position: absolute; left: 0; top: 320px; width: 1200px; display: flex; justify-content: center; align-items: center; gap: 12px; }
  .footer-brand .brand-dot { width: 28px; height: 28px; background: var(--white); }
  .footer-brand span { font-size: 30px; font-weight: 500; color: var(--white); letter-spacing: 1px; }
</style>
</head>
<body>

<header class="site-header">
  <div class="brand"><span class="brand-dot"></span><span class="brand-name">Fennow Roots</span></div>
  <nav class="main-nav">
    <a href="#" style="left:0">Home</a>
    <a href="#" style="left:62px">Shop</a>
    <a href="#" style="left:121px">About Us</a>
  </nav>
  <div class="search-box">
    <svg width="13" height="13" viewBox="0 0 13 13" fill="none" stroke="#222" stroke-width="1.4"><circle cx="5.5" cy="5.5" r="4.3"/><line x1="8.6" y1="8.6" x2="12" y2="12"/></svg>
    <span>Search</span>
  </div>
  <div class="header-icons">
    <span class="avatar"></span>
    <svg style="left:1095px;top:3px" width="20" height="18" viewBox="0 0 20 18" fill="none" stroke="#222" stroke-width="1.4"><path d="M10 16.5 2.5 9.2A4.4 4.4 0 0 1 10 3.4a4.4 4.4 0 0 1 7.5 5.8Z"/></svg>
    <svg style="left:1141px;top:1px" width="18" height="21" viewBox="0 0 18 21" fill="none" stroke="#222" stroke-width="1.3"><rect x="1.5" y="6" width="15" height="13.5"/><path d="M5.5 6V4.5a3.5 3.5 0 0 1 7 0V6"/><text x="9" y="16.5" font-size="7" text-anchor="middle" fill="#222" stroke="none" font-family="Montserrat, sans-serif">0</text></svg>
  </div>
</header>

<section class="hero">
  <h1 class="hero-title">Welcome to Fennow<br>Roots.</h1>
  <p class="hero-sub">Where the wisdom of nature meets<br>the art of healing.</p>
  <div class="product-shot" role="img" aria-label="Product photo of a jar of natural pain relief cream with white lid and blue label"></div>
</section>

<section class="features">
  <div class="feature" style="left:42px">
    <svg width="62" height="64" viewBox="0 0 62 64" fill="none" stroke="#111" stroke-width="2.2" stroke-linejoin="round"><path d="M18 4h16M21 4v16L5 52a5 5 0 0 0 4.5 7H36M31 4v16l6 12"/><path d="M11 40h20"/><circle cx="16" cy="48" r="2"/><circle cx="24" cy="45" r="1.6"/><path d="M42 38l6 3.5v7L42 52l-6-3.5v-7Z"/><path d="M50 50l6 3.5v7L50 64l-6-3.5v-7Z"/><path d="M38 52l6 3.5v5"/></svg>
    <h3>Expertly Crafted<br>Formula</h3>
    <p>Formulated by an<br>herbalist with over a<br>decade of clinical<br>experience.</p>
  </div>
  <div class="feature" style="left:430px">
    <svg width="66" height="68" viewBox="0 0 66 68" fill="none" stroke="#111" stroke-width="2.2" stroke-linejoin="round"><path d="M3 30h60a30 22 0 0 1-60 0Z"/><path d="M20 52l-3 10h32l-3-10"/><path d="M44 30l10-22 6 3-9 19"/><path d="M16 30c0-8 6-14 14-14-1 8-6 14-14 14Z"/><circle cx="16" cy="41" r="2.3"/><circle cx="26" cy="42" r="2.3"/><circle cx="36" cy="42" r="2.3"/><circle cx="46" cy="41" r="2.3"/></svg>
    <h3>Fast-Acting<br>Ingredients</h3>
    <p>With nature’s power at<br>the forefront, our 6<br>active botanicals deliver<br>almost instant relief.</p>
  </div>
  <div class="feature" style="left:818px">
    <svg width="70" height="68" viewBox="0 0 70 68" fill="none" stroke="#111" stroke-width="2.2" stroke-linejoin="round"><path d="M37 36V22"/><path d="M37 22c-2-10-10-14-18-14 0 9 8 14 18 14Z"/><path d="M37 22c2-10 10-14 18-14 0 9-8 14-18 14Z"/><path d="M2 54l12-10c5-4 10-4 15-1l11 5a3 3 0 0 1-2 6H26"/><path d="M14 62l10-4h18l22-14a4 4 0 0 0-5-6L44 46"/></svg>
    <h3>Nurturing<br>Touch</h3>
    <p>Not only does our natural pain<br>relief cream alleviate discomfort,<br>but it also nourishes and<br>rejuvenates your skin.</p>
  </div>
</section>

<section class="difference">
  <h2>Feel the Difference<br>in Just 1 Minute!</h2>
  <p>Whether you’re overcoming the strains of daily life or the demands of an active lifestyle, our natural pain relief cream is your go-to solution for quick relief.</p>
  <a class="btn-shop" href="#">SHOP NOW</a>
  <div class="product-shot" role="img" aria-label="Product photo of the pain cream jar with a white lid and pale blue label"></div>
</section>

<section class="testimonials">
  <h2>Testimonials</h2>
  <article class="quote-card" style="left:38px">
    <h4>"Better than prescription pain meds"</h4>
    <p>Fennow Roots pain cream is by far 10000000x better than any prescription pain medication that I've ever taken. So please, if you suffer from occasional neuropathies, muscle pain, back pain, elbow, shoulder.... pretty much anything related along those lines - BUY THIS ASAP!!!! You'll thank me.</p>
    <div class="author">Dana R. Bradenton, FL</div>
  </article>
  <article class="quote-card" style="left:420px">
    <h4>"Helps me sleep"</h4>
    <p>Great product! I use my cream daily and in the evening to help me sleep through my pain. Smells wonderful and the only cream my 91 year old Mom allowed me to massage on her aching shoulders. Thank you Owen Halloway❤️"</p>
    <div class="author">Marla T. Lake Tahoe, CA</div>
  </article>
  <article class="quote-card" style="left:801px">
    <h4>"This truly is the best"</h4>
    <p>It works fantastically. We have used it for neck/nerve irritation pain, knee pain, leg pain, elbow and back. Every time, complete relief! Thank you Owen Halloway for sharing your knowledge, passion and for making such a quality product!</p>
    <div class="author">Joanne W. Johnson City, TN</div>
  </article>
</section>

<footer class="contact-band">
  <h2>Have more questions?<br>We're just a message away!</h2>
  <p>Your questions matter to us, and we take pride in offeringsupport with a friendly touch. Your inquiries are always welcomed with open arms. Together, let’s explore the natural path to wellness!</p>
  <a class="btn-contact" href="#">Contact Us</a>
  <div class="footer-brand"><span class="brand-dot"></span><span>Fennow Roots</span></div>
</footer>

</body>
</html>
```